Automotive eCommerce Business looking for a business card design

Looking for a clean and simple business card design. Our company name is "Brindle Auto" and we are a company specializing in the ecommerce sales of automotive parts, specifically for pick up trucks and large SUVs. Our company colours are red, black, and white.

Feel free to use the logo provided or create a new logo that you seem fit. Looking forward to your creative ideas!

Industry/Entity Type

Automotive

Contact Information for Business Card

We were thinking of a possibly two-sided design featuring just the logo and company name on one side, and personal information on the other side. Single sided designs will be considered as well.

Font styles to use
Serif
Sans Serif
Decorative

Colors
ec1f27
ffffff
000000

Requirements
Must have
• Space for employee's name, title, phone number and email address, along with the company address and website somewhere.

```html
<!DOCTYPE html>
<html lang="en">
<head>
<meta charset="utf-8">
<title>Brindle Auto – Business Card</title>
<link rel="stylesheet" href="https://fonts.googleapis.com/css2?family=Cinzel:wght@600&family=Roboto:wght@400;500;700&display=swap">
<style>
  :root {
    --page-bg: #d9d6d3;
    --card-bg: #eeecea;
    --brand-red: #8c1d25;
    --brand-red-dark: #6e141b;
    --ink: #1e1e1e;
    --ink-soft: #2c2c2c;
  }
  * { margin: 0; padding: 0; box-sizing: border-box; }
  html, body {
    width: 1200px; height: 969px; overflow: hidden;
    background: var(--page-bg);
  }
  .card {
    position: absolute; left: 100px; top: 199px;
    width: 1000px; height: 571px;
    background: var(--card-bg);
    border-radius: 22px;
    overflow: hidden;
    font-family: "Roboto", Arial, sans-serif;
    color: var(--ink);
  }
  .brand-lockup {
    position: absolute; left: 60px; top: 110px;
    width: 460px;
    display: flex; flex-direction: column; align-items: center; gap: 34px;
  }
  .brand-square {
    width: 230px; height: 230px;
    background: linear-gradient(135deg, var(--brand-red), var(--brand-red-dark));
  }
  .brand-name {
    font-weight: 700; font-size: 40px; line-height: 44px;
    letter-spacing: 2px; color: var(--brand-red); text-transform: uppercase;
  }
  .edge-tab {
    position: absolute; left: 974px; top: 69px;
    width: 26px; height: 43px;
    background: var(--brand-red);
  }
  .person, .contact, .company { position: absolute; right: 57px; text-align: right; }
  .person { top: 72px; }
  .person-name {
    font-weight: 700; font-size: 31px; line-height: 36px;
    color: var(--brand-red); text-transform: uppercase;
  }
  .person-title {
    font-weight: 500; font-size: 23px; line-height: 30px;
    color: var(--ink-soft); text-transform: uppercase; margin-top: 4px;
  }
  .contact { top: 180px; font-size: 22px; line-height: 31.5px; }
  .address { margin-bottom: 18px; }
  .contact-line { display: flex; justify-content: flex-end; align-items: center; gap: 14px; }
  .contact-line svg { width: 20px; height: 20px; fill: var(--brand-red); flex: none; }
  .company {
    top: 446px;
    font-family: "Cinzel", Georgia, serif; font-weight: 600;
    font-size: 39px; color: var(--ink);
  }
</style>
</head>
<body>
  <div class="card">
    <div class="brand-lockup">
      <div class="brand-square"></div>
      <p class="brand-name">Brindle Auto</p>
    </div>
    <div class="edge-tab"></div>

    <div class="person">
      <p class="person-name">Daniel Reyes</p>
      <p class="person-title">CEO/Founder</p>
    </div>

    <div class="contact">
      <div class="address">
        <p>2215 Birchwood Road</p>
        <p>Fairbanks, Alaska 99701</p>
      </div>
      <p class="contact-line">907 555 0142
        <svg viewBox="0 0 24 24"><path d="M6.6 10.8a15.1 15.1 0 0 0 6.6 6.6l2.2-2.2c.3-.3.7-.4 1-.2 1.1.4 2.3.6 3.6.6.6 0 1 .4 1 1V20c0 .6-.4 1-1 1A17 17 0 0 1 3 4c0-.6.4-1 1-1h3.5c.6 0 1 .4 1 1 0 1.3.2 2.5.6 3.6.1.3 0 .7-.2 1z"/></svg>
      </p>
      <p class="contact-line">907 555 0187
        <svg viewBox="0 0 24 24"><path d="M7 1h10a2 2 0 0 1 2 2v18a2 2 0 0 1-2 2H7a2 2 0 0 1-2-2V3a2 2 0 0 1 2-2zm0 3v14h10V4zm5 15.2a1.2 1.2 0 1 0 0 2.4 1.2 1.2 0 0 0 0-2.4z"/></svg>
      </p>
      <p class="contact-line">907 555 0163
        <svg viewBox="0 0 24 24"><path d="M6 2h10l2 2v5H6zM3 10h18a2 2 0 0 1 2 2v7h-4v-4H5v4H1v-7a2 2 0 0 1 2-2zm4 6h10v6H7z"/></svg>
      </p>
      <p class="contact-line">daniel@brindleauto.com
        <svg viewBox="0 0 24 24"><path d="M2 5h20v14H2zm2 2v.5l8 5.2 8-5.2V7zm0 2.8V17h16V9.8l-8 5.2z"/></svg>
      </p>
      <p class="contact-line">www.brindleauto.com
        <svg viewBox="0 0 24 24"><path d="M12 2a10 10 0 1 0 0 20 10 10 0 0 0 0-20zm-1 17.9A8 8 0 0 1 4 12l1-1 4 4v1l2 2zm6.9-2.5A2 2 0 0 0 16 16h-1v-3a1 1 0 0 0-1-1H8v-2h2a1 1 0 0 0 1-1V7h2a2 2 0 0 0 2-2v-.4a8 8 0 0 1 2.9 12.8z"/></svg>
      </p>
    </div>

    <p class="company">Brindle Auto Ltd.</p>
  </div>
</body>
</html>
```